SkyvornQ Business Cards and Stationary Design

Need a design for our business cards and stationary. I want to carry on the theme of the logo. I want the business cards to have a design on the back. I would like the business cards and the stationary to carry the same theme, design scheme, and branding

Target Market(s)

Airlines and Maintenance Facilities

Industry/Entity Type

Aviation

Contact Information for Business Card

Name
Position Title
Address: 4827 Trellis Hollow Road, Fort Pierce, Florida, 34951
Office Number
Mobile Number
Email
Website

Font styles to use
Serif
Sans Serif

Colors

Designer to choose colors to be used in the design.

```html
<!DOCTYPE html>
<html lang="en">
<head>
<meta charset="utf-8">
<title>SkyvornQ Business Card</title>
<link href="https://fonts.googleapis.com/css2?family=Jost:wght@400;500;600&family=Open+Sans:wght@400&display=swap" rel="stylesheet">
<style>
  :root {
    --navy: #0b2a52;
    --navy-deep: #082549;
    --sky: #1a9ad8;
    --royal: #0f4f92;
    --paper: #ffffff;
    --backdrop: #e7e9ec;
    --ink-soft: #2b3440;
  }
  * { margin: 0; padding: 0; box-sizing: border-box; }
  html, body { width: 1200px; height: 872px; overflow: hidden; }
  body {
    background: var(--backdrop);
    font-family: "Open Sans", sans-serif;
    position: relative;
  }
  .card {
    position: absolute;
    left: 250px;
    width: 700px;
    height: 400px;
    background: var(--paper);
    overflow: hidden;
    box-shadow: 0 2px 10px rgba(0,0,0,0.12);
  }
  .card--back { top: 24px; }
  .card--front { top: 448px; }

  /* Back side */
  .back-brand {
    position: absolute;
    left: 0; right: 0; top: 140px;
    display: flex;
    align-items: center;
    justify-content: center;
    gap: 18px;
  }
  .brand-ring {
    width: 58px; height: 58px;
    border: 5px solid var(--sky);
    border-radius: 50%;
  }
  .brand-name {
    font-family: "Jost", sans-serif;
    font-weight: 600;
    color: var(--navy);
    letter-spacing: 8px;
    text-transform: uppercase;
  }
  .back-brand .brand-name { font-size: 46px; }
  .back-web {
    position: absolute;
    left: 0; right: 0; top: 232px;
    text-align: center;
    font-size: 16px;
    letter-spacing: 5px;
    color: var(--ink-soft);
  }

  /* Front side */
  .front-brand .brand-ring {
    position: absolute;
    left: 172px; top: 42px;
    width: 86px; height: 86px;
    border-width: 6px;
  }
  .front-brand .brand-name {
    position: absolute;
    left: 60px; top: 140px;
    font-size: 42px;
  }
  .contact-band {
    position: absolute;
    left: 300px; top: 198px;
    width: 400px; height: 112px;
    background: var(--navy-deep);
  }
  .person-band {
    position: absolute;
    left: 0; top: 250px;
    width: 352px; height: 88px;
    background: linear-gradient(90deg, var(--navy) 0%, var(--royal) 55%, var(--sky) 100%);
    padding: 16px 0 0 40px;
    color: var(--paper);
    font-family: "Jost", sans-serif;
  }
  .person-name { font-size: 24px; font-weight: 500; text-transform: uppercase; line-height: 1.2; }
  .person-title { font-size: 20px; font-weight: 400; text-transform: uppercase; line-height: 1.3; }
  .contact-list {
    position: absolute;
    left: 358px; top: 205px;
    list-style: none;
    color: var(--paper);
    font-size: 15px;
  }
  .contact-list li {
    display: flex; align-items: center; gap: 12px;
    height: 24px;
  }
  .contact-icon { width: 16px; height: 16px; flex: none; }
  .address {
    position: absolute;
    left: 40px; top: 360px;
    display: flex; align-items: center; gap: 8px;
    font-size: 15px;
    color: var(--ink-soft);
  }
</style>
</head>
<body>

<section class="card card--back" aria-label="Card back">
  <div class="back-brand">
    <span class="brand-ring"></span>
    <span class="brand-name">SkyvornQ</span>
  </div>
  <p class="back-web">www.skyvornq.com</p>
</section>

<section class="card card--front" aria-label="Card front">
  <div class="front-brand">
    <span class="brand-ring"></span>
    <span class="brand-name">SkyvornQ</span>
  </div>

  <div class="contact-band"></div>
  <div class="person-band">
    <p class="person-name">Darren Kolbeck</p>
    <p class="person-title">President</p>
  </div>

  <ul class="contact-list">
    <li>
      <svg class="contact-icon" viewBox="0 0 16 16" fill="none" stroke="#fff" stroke-width="1.3"><circle cx="8" cy="8" r="7"/><path d="M5.5 4.5l1.3 1.6-.8 1c.5 1 1.3 1.8 2.3 2.3l1-.8 1.6 1.3-.8 1.1c-2.8-.4-4.9-2.5-5.3-5.3z" fill="#fff"/></svg>
      772-555-0148
    </li>
    <li>
      <svg class="contact-icon" viewBox="0 0 16 16" fill="none" stroke="#fff" stroke-width="1.3"><circle cx="8" cy="8" r="7"/><rect x="5.5" y="3.8" width="5" height="8.4" rx="1"/></svg>
      772-555-0193
    </li>
    <li>
      <svg class="contact-icon" viewBox="0 0 16 16" fill="none" stroke="#fff" stroke-width="1.3"><circle cx="8" cy="8" r="7"/><rect x="4" y="5.2" width="8" height="5.6"/><path d="M4 5.5l4 3 4-3"/></svg>
      info@skyvornq.com
    </li>
    <li>
      <svg class="contact-icon" viewBox="0 0 16 16" fill="none" stroke="#fff" stroke-width="1.2"><circle cx="8" cy="8" r="7"/><ellipse cx="8" cy="8" rx="3" ry="7"/><path d="M1 8h14M2.5 4.5h11M2.5 11.5h11"/></svg>
      www.skyvornq.com
    </li>
  </ul>

  <p class="address">
    <svg class="contact-icon" viewBox="0 0 16 16" fill="none" stroke="#0f4f92" stroke-width="1.4"><path d="M8 15s5-5 5-8.5A5 5 0 0 0 3 6.5C3 10 8 15 8 15z"/><circle cx="8" cy="6.5" r="1.8"/></svg>
    4827 Trellis Hollow Road, Fort Pierce, Florida, 34951
  </p>
</section>

</body>
</html>
```